Quiet Hollow is a cabin in Gatlinburg, Tennessee, near the Ferncrest Ridge National Park. When our cabin was built, there was one thing more important than any other--peace. The front of our cabin is surrounded by woods. It has a huge deck with a swing, Adirondack chairs, and a love seat for relaxation. The back deck has a hot tub, a large round glass table for cocktails or dinner, and because we left no stone unturned, we have a telescope for stargazing. There are two master suites, each have a private bath with a large jetted tub, seperate shower, flat screen TV, and a door that leads to the back deck.

Industry/Entity Type

Business

Contact Information for Business Card

Quiet Hollow Vacation Rentals, LLC
871 Belford Crest Pl.
Oakland, Ky 42159
Janet M. Pruitt, Owner/Manager
(270) 614.2087

```html
<!DOCTYPE html>
<html lang="en">
<head>
<meta charset="utf-8">
<title>Quiet Hollow Vacation Rentals – Business Card</title>
<link rel="stylesheet" href="https://fonts.googleapis.com/css2?family=Raleway:wght@400;500;600&display=swap">
<style>
  :root {
    --backdrop: #1b1b1d;
    --card: #2f3035;
    --ring: #3a3b40;
    --accent-green: #3db84a;
    --text-light: #d2d2d4;
    --text-silver: #c4c5c8;
  }
  html, body {
    margin: 0;
    padding: 0;
    width: 1200px;
    height: 900px;
    overflow: hidden;
    background: var(--backdrop);
    font-family: "Raleway", Arial, sans-serif;
  }
  .canvas {
    position: relative;
    width: 1200px;
    height: 900px;
  }
  .card {
    position: absolute;
    left: 330px;
    width: 543px;
    height: 315px;
    background: var(--card);
    border-radius: 14px;
  }
  .card--front { top: 121px; }
  .card--back { top: 487px; }

  .brand-circle {
    position: absolute;
    border-radius: 50%;
    border: 3px solid var(--ring);
    box-sizing: border-box;
    display: flex;
    align-items: center;
    justify-content: center;
  }
  .card--front .brand-circle {
    left: 99px;
    top: 100px;
    width: 116px;
    height: 116px;
  }
  .brand-name-small {
    color: var(--accent-green);
    font-weight: 500;
    font-size: 15px;
    text-align: center;
    line-height: 1.2;
  }

  .contact {
    position: absolute;
    left: 282px;
    top: 114px;
  }
  .contact__name {
    margin: 0;
    color: var(--accent-green);
    font-weight: 400;
    font-size: 25px;
    line-height: 30px;
  }
  .contact__role {
    margin: 0;
    color: var(--text-light);
    font-size: 16px;
    line-height: 20px;
  }
  .contact__details {
    margin: 19px 0 0 3px;
    color: var(--text-light);
    font-size: 14px;
    line-height: 18px;
  }
  .contact__details p { margin: 0; }

  .card--back .brand-circle {
    left: 224px;
    top: 80px;
    width: 86px;
    height: 86px;
  }
  .brand-name {
    position: absolute;
    left: 0;
    right: 0;
    top: 182px;
    margin: 0;
    text-align: center;
    color: var(--text-silver);
    font-weight: 600;
    font-size: 19px;
    letter-spacing: 0.3px;
  }
</style>
</head>
<body>
<main class="canvas">
  <section class="card card--front">
    <div class="brand-circle">
      <span class="brand-name-small">Quiet<br>Hollow</span>
    </div>
    <div class="contact">
      <h1 class="contact__name">Janet M. Pruitt</h1>
      <p class="contact__role">Owner/Manager</p>
      <div class="contact__details">
        <p>871 Belford Crest Pl.</p>
        <p>Oakland, Ky 42159</p>
        <p>(270) 614.2087</p>
      </div>
    </div>
  </section>

  <section class="card card--back">
    <div class="brand-circle"></div>
    <p class="brand-name">Quiet Hollow Vacation Rentals, LLC</p>
  </section>
</main>
</body>
</html>
```